Unlock Your Way Upward Promotional Flyer

I Need a one page, one-sided 8.5 x 11 editable promotional flyer that POPS!, designed in photoshop

[TITLE]Unlock Your Way Upward: 3 BOLD Moves to Up-Level Your Business Now!

[CONTENT for the Flyer:]

At this content-rich event you will learn how to:
• Get out of feast and famine mode and into six, multi-six and/or seven figure-income mode
• Leapfrog your competition and become the obvious choice in your market
• Have your business aligned with who you are and what you want
• Enjoy your business far more than you imagined possible.
• Have more fun and time to yourself
• Live free and unbound!

Accolades
“Delphine helped us increase our six figure income by 41%...I feel reborn!” Marlene & Curtis Pettibone, Vienna, VA

“…Delphine is a joy to listen to - compelling, smart, provocative…” – Dennis Whitcombe, Charlotte, North Carolina

“Delphine helped me increase my business by 66%...without me spending more time, money, or making cold calls! …I am in the zone!” Kay Standish, Baltimore, MD
“Delphine is an energetic and dynamic speaker…content-rich…holds your attention to the very end!” Walt Pruitt, Frmr Pres., Hale & Brandt, MD, MD, D.C., PA, DE, NJ
“Delphine is the real estate whisperer!” Tom Garvey, Washington D.C.

“Delphine was prepared, funny, informative and made a connection with each of our agents…Fabulous!…even my admins were PUMPED!!! – Paul Denholm, New York

About Delphine:
Delphine is a highly regarded business development speaker & coach who knows how to pump up an audience and have them making more money, in less time, AND having more fun doing it! What’s not to love?! Consistently rated as an exceptional speaker and conference favorite! Among her work: Standing Apart: How to Draw Your Perfect Buyers Time After Time!, Finding Buyers Without Fuss, The Worst Outreach Errors Real Estate Agents Commit and How to Sidestep Them, Hard Seasons Build Hardy Brokers, Drive Within for Real Estate Agents.

[Also need a section for:]
Date: December 9, 2015, Time: 9:00 Am - 12:00 Noon, Place: Copper Lantern Convention, Ashford Mill, PA

Target Market(s)

Real Estate Agents

Industry/Entity Type

Real Estate Agent

Font styles to use
Sans Serif

Colors
0655a3
f37122

Requirements
Must have
• the top tier property mentor logo
Nice to have
• unlock your way upward logo; lots of POP! :-) ; open to other colors, accent colors.

```html
<!DOCTYPE html>
<html lang="en">
<head>
<meta charset="utf-8">
<title>Unlock Your Way Upward – Event Flyer</title>
<link rel="stylesheet" href="https://fonts.googleapis.com/css2?family=Anton&family=Oswald:wght@600;700&family=Fira+Sans+Condensed:wght@500;600;700&family=Open+Sans:wght@400;600;700&display=swap">
<style>
  :root {
    --navy: #1f2257;
    --orange: #f37122;
    --orange-deep: #ea5a1c;
    --gold: #f8b82e;
    --silver: #b9bcc4;
    --ink: #1c1c1c;
    --paper: #ffffff;
    --rule: #f2a35c;
  }
  * { margin: 0; padding: 0; box-sizing: border-box; }
  html, body { width: 965px; height: 1200px; overflow: hidden; background: var(--paper); }
  .flyer { position: relative; width: 965px; height: 1200px; overflow: hidden; font-family: "Open Sans", Arial, sans-serif; color: var(--ink); }
  .backdrop { position: absolute; inset: 0; }

  .title { position: absolute; left: 78px; top: 32px; font-family: "Anton", Impact, sans-serif; font-size: 76px; line-height: 1; color: #fff; letter-spacing: 1px; text-shadow: 2px 3px 4px rgba(0,0,0,.35); }
  .subtitle { position: absolute; left: 78px; top: 128px; font-family: "Fira Sans Condensed", Arial, sans-serif; font-weight: 600; font-size: 33px; color: #fff; text-shadow: 1px 2px 3px rgba(0,0,0,.35); }

  .brand { position: absolute; left: 50px; top: 330px; width: 330px; text-align: center; font-family: "Open Sans", Arial, sans-serif; font-weight: 600; font-size: 33px; line-height: 1.15; color: #fff; }

  .event { position: absolute; left: 40px; top: 458px; width: 300px; text-align: center; }
  .event-date { font-family: "Oswald", Impact, sans-serif; font-weight: 700; font-size: 38px; line-height: 50px; color: var(--gold); border-bottom: 1px solid var(--gold); }
  .event-time { font-family: "Oswald", Impact, sans-serif; font-weight: 600; font-size: 30px; line-height: 46px; color: #fff; border-bottom: 1px solid var(--gold); }
  .event-place { margin-top: 8px; font-family: "Oswald", Impact, sans-serif; font-weight: 600; font-size: 21px; line-height: 29px; color: var(--gold); }

  .learn { position: absolute; left: 453px; top: 282px; width: 480px; color: #fff; }
  .learn h2 { font-family: "Fira Sans Condensed", Arial, sans-serif; font-weight: 600; font-size: 24px; margin-bottom: 12px; }
  .learn ul { list-style: none; }
  .learn li { position: relative; padding-left: 28px; font-size: 16px; line-height: 20px; margin-bottom: 6px; }
  .learn li::before { content: ""; position: absolute; left: 2px; top: 4px; width: 12px; height: 12px; border-radius: 50%; background: radial-gradient(circle at 35% 35%, #ffe08a, var(--gold) 55%, #d98a10); }

  .coach-photo { position: absolute; left: 730px; top: 585px; width: 235px; height: 236px; }
  .coach-name { position: absolute; left: 488px; top: 622px; width: 245px; text-align: center; font-family: "Open Sans", Arial, sans-serif; font-weight: 600; font-size: 30px; color: #d9d9d9; text-shadow: 1px 1px 0 #777, 0 2px 4px rgba(0,0,0,.4); }
  .mentor-mark { position: absolute; left: 462px; top: 672px; width: 285px; text-align: center; font-family: "Fira Sans Condensed", Arial, sans-serif; font-weight: 700; color: var(--gold); line-height: 1; }
  .mentor-mark .big { display: block; font-size: 56px; }
  .mentor-mark .small { display: block; font-size: 27px; margin-top: 4px; }

  .accolades { position: absolute; left: 40px; top: 700px; width: 445px; font-size: 13.5px; line-height: 18px; }
  .accolades h2 { font-weight: 400; font-size: 26px; color: var(--navy); margin-bottom: 18px; }
  .quote { padding-bottom: 9px; margin-bottom: 9px; border-bottom: 1px solid var(--rule); }
  .quote.plain { border-bottom: none; margin-bottom: 6px; padding-bottom: 0; }
  .quote cite { display: block; font-style: normal; font-weight: 700; margin-top: 6px; }

  .about { position: absolute; left: 521px; top: 850px; width: 400px; }
  .about h2 { text-align: center; font-weight: 400; font-size: 25px; color: var(--navy); margin-bottom: 14px; }
  .about p { font-size: 14.5px; line-height: 20.7px; text-align: justify; }

  .tagline { position: absolute; left: 81px; top: 1152px; font-family: "Fira Sans Condensed", Arial, sans-serif; font-weight: 600; font-size: 29px; color: #fff; }
</style>
</head>
<body>
<main class="flyer">
  <svg class="backdrop" width="965" height="1200" viewBox="0 0 965 1200" aria-hidden="true">
    <defs>
      <linearGradient id="orangeFade" x1="0" y1="0" x2="1" y2="0">
        <stop offset="0" stop-color="#f7892f"/><stop offset="1" stop-color="#f26a1e"/>
      </linearGradient>
      <linearGradient id="silverSweep" x1="0" y1="0" x2="1" y2="0">
        <stop offset="0" stop-color="#e6e7ea"/><stop offset=".5" stop-color="#9a9da6"/><stop offset="1" stop-color="#e0e1e5"/>
      </linearGradient>
    </defs>
    <!-- navy field -->
    <path d="M0,60 H965 V590 C860,560 780,575 700,605 C560,660 420,670 300,660 C180,650 80,630 0,620 Z" fill="var(--navy)"/>
    <!-- orange strip under navy -->
    <path d="M0,620 C80,630 180,650 300,660 C420,670 560,660 700,605 C780,575 860,560 965,590 V612 C860,585 780,600 700,630 C560,685 420,700 300,690 C180,680 80,665 0,650 Z" fill="var(--orange)"/>
    <!-- silver sweep under top band -->
    <path d="M0,80 C180,290 380,345 560,300 C700,265 820,205 965,240 V228 C820,195 700,252 560,287 C380,332 180,272 0,70 Z" fill="url(#silverSweep)"/>
    <!-- top orange band -->
    <path d="M0,0 H965 V226 C820,192 700,250 560,285 C380,330 180,270 0,72 Z" fill="url(#orangeFade)"/>
    <!-- column divider -->
    <line x1="437" y1="300" x2="437" y2="570" stroke="#2e3270" stroke-width="1"/>
    <!-- grey frame around mentor panel -->
    <polyline points="351,650 513,821 965,821" fill="none" stroke="#c9cacd" stroke-width="3"/>
    <!-- bottom band -->
    <path d="M0,1186 C200,1118 520,1112 965,1142 V1155 C520,1128 200,1134 0,1200 Z" fill="url(#silverSweep)"/>
    <path d="M0,1200 C200,1134 520,1128 965,1155 V1200 Z" fill="var(--orange-deep)"/>
  </svg>

  <h1 class="title">Unlock Your Way Upward</h1>
  <p class="subtitle">3 BOLD MOVES TO UP-LEVEL YOUR BUSINESS NOW!</p>

  <div class="brand">Unlock Your Way Upward</div>

  <section class="event">
    <div class="event-date">December 9, 2015</div>
    <div class="event-time">9:00 AM - 12:00 Noon</div>
    <div class="event-place">Copper Lantern Convention,<br>Ashford Mill, PA</div>
  </section>

  <section class="learn">
    <h2>At this content-rich event you will learn how to:</h2>
    <ul>
      <li>Get out of feast and famine mode and into six, multi-six and/or seven figure-income mode</li>
      <li>Leapfrog your competition and become the obvious choice in your market</li>
      <li>Have your business aligned with who you are and what you want</li>
      <li>Enjoy your business far more than you imagined possible.</li>
      <li>Have more fun and time to yourself</li>
      <li>Live free and unbound!</li>
    </ul>
  </section>

  <svg class="coach-photo" viewBox="0 0 235 236" role="img" aria-label="Portrait photo of coach Delphine Marsh in a dark blazer">
    <defs>
      <linearGradient id="portraitTone" x1="0" y1="0" x2="0" y2="1">
        <stop offset="0" stop-color="#f4f2ef"/><stop offset=".55" stop-color="#d8b69a"/><stop offset="1" stop-color="#2a2a2e"/>
      </linearGradient>
    </defs>
    <rect width="235" height="236" fill="url(#portraitTone)"/>
  </svg>

  <div class="coach-name">Delphine Marsh</div>
  <div class="mentor-mark"><span class="big">TOP TIER</span><span class="small">PROPERTY MENTOR</span></div>

  <section class="accolades">
    <h2>Accolades</h2>
    <div class="quote">“Delphine is a joy to listen to - compelling, smart, provocative”<cite>Dennis Whitcombe, Charlotte, North Carolina</cite></div>
    <div class="quote">“Delphine helped us increase our six figure income by 41%...I feel reborn!”<cite>Marlene &amp; Curtis Pettibone, Vienna, VA</cite></div>
    <div class="quote plain">“Delphine helped me increase my business by 66%...without me spending more time, money, or making cold calls! ...I am in the zone!” Kay Standish, Baltimore, MD</div>
    <div class="quote plain">“Delphine is an energetic and dynamic speaker...content-rich...holds your attention to the very end!” Walt Pruitt, Frmr Pres., Hale &amp; Brandt, MD, D.C., PA, DE, NJ</div>
    <div class="quote">“Delphine is the real estate whisperer!”<cite>Tom Garvey, Washington D.C.</cite></div>
    <div class="quote plain">“Delphine was prepared, funny, informative and made a connection with each of our agents...Fabulous!...even my admins were PUMPED!!!<cite>Paul Denholm, New York</cite></div>
  </section>

  <section class="about">
    <h2>About Delphine</h2>
    <p>Delphine is a highly regarded business development speaker &amp; coach who knows how to pump up an audience and have them making more money, in less time, AND having more fun doing it! What’s not to love?! Consistently rated as an exceptional speaker and conference favorite! Among her work: Standing Apart: How to Draw Your Perfect Buyers Time After Time!, Finding Buyers Without Fuss, The Worst Outreach Errors Real Estate Agents Commit and How to Sidestep Them, Hard Seasons Build Hardy Brokers, Drive Within for Real Estate Agents.</p>
  </section>

  <p class="tagline">“America’s Top Tier Property Mentor”™</p>
</main>
</body>
</html>
```